Brintel Works - Fast, Efficient and Gas Mainteance for Domestic, Commercial and Industrial clients

We are in the process of purchasing a new business and would like to get a new logo and business card.
Business is a gas maintenance business that also does new gas installations.
Has been established since 1988.
Services include:
Install all types of gas appliances & equipment inc. hot water units
Maintain / repair / replace all types of gas appliances & equipment

Target Market(s)

Domestic, Commercial and Industrial clients

Industry/Entity Type

Business

Contact Information for Business Card

admin@brintelworks.com.au
07 3918 4726
Brintel Works PTY LTD

Logo Text

Gas Fitting & Plumbing Maintenance Specialists

Font styles to use
Sans Serif

Requirements
Must have
• Logo
• Business name, contact number, email address, web address
• Domestic | Commercial | Industrial Est Since 1988
Nice to have
• Possibly a black card with a flame logo to one side
Should not have
• Spelling errors

```html
<!DOCTYPE html>
<html lang="en">
<head>
<meta charset="utf-8">
<title>Brintel Works – Business Card</title>
<link rel="stylesheet" href="https://fonts.googleapis.com/css2?family=Open+Sans:wght@400&family=Questrial&family=Cinzel:wght@400&display=swap">
<style>
  :root {
    --backdrop: #e9e6e2;
    --card-black: #000000;
    --wave-yellow: #fdd20a;
    --wave-orange-top: #f9c31e;
    --wave-orange-bottom: #f08a1f;
    --brand-yellow: #f6c21a;
    --tagline-orange: #d9701f;
    --mark-orange: #f07d1f;
    --contact-white: #ffffff;
  }
  html, body {
    margin: 0;
    width: 1200px;
    height: 900px;
    overflow: hidden;
    background: var(--backdrop);
  }
  .canvas {
    position: relative;
    width: 1200px;
    height: 900px;
  }
  .business-card {
    position: absolute;
    left: 150px;
    top: 172px;
    width: 900px;
    height: 555px;
    box-shadow: 0 10px 30px rgba(0,0,0,0.18);
  }
  .brand-name {
    font-family: "Questrial", sans-serif;
    font-size: 38px;
    letter-spacing: 1px;
    fill: var(--brand-yellow);
  }
  .brand-subtitle {
    font-family: "Cinzel", serif;
    font-size: 12.5px;
    letter-spacing: 1.6px;
    fill: var(--tagline-orange);
  }
  .contact-line {
    font-family: "Open Sans", sans-serif;
    font-size: 17px;
    fill: var(--contact-white);
  }
  .contact-icon {
    fill: var(--contact-white);
  }
</style>
</head>
<body>
<main class="canvas">
  <svg class="business-card" viewBox="0 0 652 402" xmlns="http://www.w3.org/2000/svg" aria-label="Brintel Works business card">
    <defs>
      <linearGradient id="wave-fill" x1="0" y1="0" x2="0" y2="1">
        <stop offset="0" stop-color="var(--wave-orange-top)"/>
        <stop offset="1" stop-color="var(--wave-orange-bottom)"/>
      </linearGradient>
    </defs>

    <rect class="card-face" width="652" height="402" fill="var(--card-black)"/>

    <g class="wave-band">
      <path fill="var(--wave-yellow)" d="M0,210 C50,266 110,300 170,296 C280,290 420,110 560,111 C605,112 634,140 652,160 L652,402 L0,402 Z"/>
      <path fill="var(--card-black)" d="M0,222 C50,278 110,310 170,306 C280,300 420,126 560,127 C604,128 634,152 652,172 L652,402 L0,402 Z"/>
      <path fill="url(#wave-fill)" d="M0,232 C50,290 110,320 170,316 C280,310 420,136 560,137 C604,138 634,162 652,182 L652,402 L0,402 Z"/>
    </g>

    <g class="brand-lockup" text-anchor="middle">
      <circle class="brand-dot" cx="175" cy="110" r="14" fill="var(--mark-orange)"/>
      <text class="brand-name" x="176" y="217">BRINTEL</text>
      <text class="brand-subtitle" x="176" y="242">WORKS PTY LTD</text>
    </g>

    <g class="contact-block" text-anchor="end">
      <text class="contact-line" x="616" y="228">12345, Address Goes Here</text>
      <text class="contact-line" x="616" y="254">Country Name, 123456</text>

      <text class="contact-line" x="592" y="310">07 3918 4726</text>
      <text class="contact-line" x="592" y="338">admin@brintelworks.com.au</text>
      <text class="contact-line" x="592" y="366">www.brintelworks.com.au</text>
    </g>

    <g class="contact-icons">
      <path class="contact-icon icon-phone" d="M602,299 c1.5,-1 3,-1 3.5,0 l1.8,2.6 c0.5,0.8 0.2,1.6 -0.6,2.1 l-1,0.6 c0.8,1.8 2.2,3.3 4,4.2 l0.7,-1 c0.5,-0.8 1.4,-1 2.1,-0.5 l2.5,1.8 c0.9,0.6 0.8,2 -0.2,3 c-1.4,1.4 -3.2,1.6 -5.2,0.6 c-3.8,-2 -6.8,-5.2 -8.4,-9 c-0.8,-1.8 -0.4,-3.3 0.8,-4.4 z"/>
      <g class="contact-icon icon-mail">
        <rect x="601" y="328" width="13" height="9.5" rx="1"/>
        <path d="M601.5,329 L607.5,333.6 L613.5,329" fill="none" stroke="#f4a51c" stroke-width="1.2"/>
      </g>
      <g class="icon-link" fill="none" stroke="var(--contact-white)" stroke-width="1.8" stroke-linecap="round">
        <path d="M605.5,362.5 l-2,2 a2.6,2.6 0 0 0 3.7,3.7 l2,-2"/>
        <path d="M609.5,358.5 l2,-2 a2.6,2.6 0 0 1 3.7,3.7 l-2,2"/>
        <path d="M606.5,365.5 l5.5,-5.5"/>
      </g>
    </g>
  </svg>
</main>
</body>
</html>
```